American cannabis tech company business card design

Pavrel.com is seeking a modern, professional, and brand-aligned business card that represents our company and its core values: Mission, Story, Values, and Impact. As an innovative cannabis company, we want a business card that is not only visually appealing but also serves as a representation of who we are and what we stand for.

Project Scope: Design a double-sided business card that integrates our brand identity and core values. Incorporate our key brand elements, ensuring a sleek and contemporary aesthetic. Visually reflect our core values (Mission, Story, Values, Impact) in a way that is engaging yet professional.

Target Market(s)

Vendors, third parties,

Contact Information for Business Card

Contact details (name, title, email, phone, website, etc.)

Font styles to use
Other font styles liked:
• Caslon, Centra

Colors

Designer to choose colors to be used in the design.

Requirements
Must have
• Pavrel.com logo and branding A creative yet clean way to integrate our core values (Mission, Story, Values, Impact) Modern typography and a well-structured layout
Nice to have
• forest green, grey, white, black
Should not have
• references to marijuana, leafs, plants, or related product

```html
<!DOCTYPE html>
<html lang="en">
<head>
<meta charset="utf-8">
<title>Pavrel.com Business Card</title>
<link href="https://fonts.googleapis.com/css2?family=Poppins:wght@400;600;700&display=swap" rel="stylesheet">
<style>
  :root {
    --backdrop: #2e2e2e;
    --card: #ffffff;
    --forest: #173018;
    --ink: #1d2a1d;
    --rule: #9aa59a;
  }
  * { margin: 0; padding: 0; box-sizing: border-box; }
  html, body {
    width: 1093px;
    height: 1200px;
    overflow: hidden;
    background: var(--backdrop);
    font-family: "Poppins", sans-serif;
    color: var(--ink);
  }
  .card {
    position: absolute;
    background: var(--card);
    border-radius: 22px;
  }
  .card--front { left: 265px; top: 226px; width: 577px; height: 356px; }
  .card--back  { left: 265px; top: 621px; width: 581px; height: 356px; }

  .wordmark {
    position: absolute;
    font-weight: 700;
    color: var(--forest);
    letter-spacing: 0.5px;
    line-height: 1;
  }
  .card--front .wordmark { left: 37px; top: 152px; font-size: 50px; }
  .card--back .wordmark {
    left: 0; right: 0; top: 146px;
    text-align: center; font-size: 70px;
  }

  .divider {
    position: absolute;
    left: 289px; top: 74px;
    width: 1px; height: 209px;
    background: linear-gradient(to bottom, transparent, var(--rule) 20%, var(--rule) 80%, transparent);
  }

  .details { position: absolute; left: 311px; top: 88px; }
  .person-name {
    font-weight: 600;
    font-size: 22px;
    line-height: 26px;
    color: var(--forest);
  }
  .person-title { font-size: 16px; line-height: 18px; }

  .contact-list { list-style: none; margin-top: 15px; }
  .contact-list li {
    display: flex; align-items: center;
    font-size: 16.5px; line-height: 21px;
  }
  .contact-list svg { width: 14px; height: 14px; margin-right: 8px; flex: none; }

  .address { margin-top: 13px; font-size: 16.5px; line-height: 21px; }
</style>
</head>
<body>
  <section class="card card--front">
    <div class="wordmark">PAVREL</div>
    <div class="divider"></div>
    <div class="details">
      <h1 class="person-name">JONATHAN SMITH</h1>
      <p class="person-title">Managing Director</p>
      <ul class="contact-list">
        <li>
          <svg viewBox="0 0 16 16" aria-hidden="true"><path d="M3 1.5l2.5 0 1.2 3.2-1.6 1.3a8 8 0 0 0 4.9 4.9l1.3-1.6 3.2 1.2 0 2.5c0 .8-.7 1.5-1.5 1.5A12.5 12.5 0 0 1 1.5 3c0-.8.7-1.5 1.5-1.5z" fill="none" stroke="currentColor" stroke-width="1.5"/></svg>
          044-123 456 789
        </li>
        <li>
          <svg viewBox="0 0 16 16" aria-hidden="true"><rect x="1" y="3" width="14" height="10" fill="currentColor"/><path d="M1 3l7 6 7-6" fill="none" stroke="#fff" stroke-width="1.3"/></svg>
          info@pavrel.com
        </li>
        <li>
          <svg viewBox="0 0 16 16" aria-hidden="true"><g fill="none" stroke="currentColor" stroke-width="1.2"><circle cx="8" cy="8" r="6.5"/><ellipse cx="8" cy="8" rx="2.8" ry="6.5"/><path d="M1.5 8h13M2.5 4.7h11M2.5 11.3h11"/></g></svg>
          www.pavrel.com
        </li>
      </ul>
      <p class="address">421, Address line goes here<br>45452,Country Name</p>
    </div>
  </section>

  <section class="card card--back">
    <div class="wordmark">PAVREL</div>
  </section>
</body>
</html>
```